Boho Flower and Curiosities Shop Needs a Non-tradtional Calendar of Events

Hi! I own a cute flower shop called Meadowlark Petals. I have lots of things going on at the shop and I'd love a calendar of events poster to put around town. I already have dates and times and descriptions. I have a very boho aesthetic, creative, whimsical and different. I'd like this calendar of events to be not cookie cutter. Something interesting with images and interesting font that matches my logo. Not a super busy design.

My events can be found here: https://www.meadowlarkpetals.example/calendar-of-events

I want to be able to easily edit the poster so I can use it in the future.

Target Market(s)

Locals who want an alternative something to do.

Industry/Entity Type

Shop

Colors

Designer to choose colors to be used in the design.

Requirements
Must have
• must have the same kind of vibe that my logo and especially the mural on my building has (I submitted an image of the building). Unique, not cheesy.
• Must be editable so I can use it in the future.
Nice to have
• I want it to have a call to action such as visit my website "www.meadowlarkpetals.example". Also I like the idea of calling it Shop Happenings instead of Events Calendar.
• It might be cool to have the events coming off of a dream catcher like (but not exactly in fact I think it can be more whimsical and perhaps my logo in the middle of the catcher) the one attached.
Should not have
• If you do include flowers - no roses or daisies! Please.

```html
<!DOCTYPE html>
<html lang="en">
<head>
<meta charset="utf-8">
<title>Shop Happenings – Meadowlark Petals</title>
<link href="https://fonts.googleapis.com/css2?family=Open+Sans:wght@400;600&family=Kaushan+Script&display=swap" rel="stylesheet">
<style>
  :root{
    --backdrop:#d9dadd;
    --paper:#ffffff;
    --ink:#1a1a1a;
    --title-text:#3a3a3a;
    --detail-text:#7a7a7a;
    --accent-orange:#e67f45;
    --accent-green:#8cc63f;
    --pale-green:#e1eebf;
    --blush:#e3adb5;
    --peach:#f7cbb0;
    --leaf:#9cc79a;
  }
  *{box-sizing:border-box;margin:0;padding:0}
  html,body{width:1163px;height:1200px;overflow:hidden;background:var(--backdrop)}
  .poster{
    position:absolute;left:158px;top:0;width:800px;height:1133px;
    background:var(--paper);overflow:hidden;
    transform:scale(1.0591);transform-origin:top left;
    font-family:"Open Sans",Arial,sans-serif;
  }
  .header-stripe{position:absolute;left:0;top:24px;width:460px;height:8px;
    background:linear-gradient(90deg,var(--accent-orange),rgba(230,127,69,0))}
  .header-band{position:absolute;left:0;top:32px;width:540px;height:87px;
    background:linear-gradient(90deg,var(--accent-green) 0%,#c5e19f 55%,rgba(255,255,255,0) 100%)}
  .poster-title{position:absolute;z-index:3;left:46px;top:30px;font-family:"Kaushan Script",cursive;
    font-size:56px;font-weight:400;color:var(--ink);line-height:1.3;white-space:nowrap}
  .floral{position:absolute;z-index:1}
  .floral-top{left:450px;top:0;width:350px;height:320px;
    background:radial-gradient(circle at 72% 20%,var(--peach) 0 18%,rgba(247,203,176,0) 32%),
               radial-gradient(ellipse at 40% 15%,var(--leaf) 0 20%,rgba(156,199,154,0) 45%),
               radial-gradient(ellipse at 92% 70%,#b8d6a8 0 12%,rgba(184,214,168,0) 30%)}
  .floral-bottom{left:0;top:800px;width:440px;height:333px;
    background:radial-gradient(circle at 28% 75%,var(--peach) 0 18%,rgba(247,203,176,0) 34%),
               radial-gradient(ellipse at 60% 85%,var(--leaf) 0 20%,rgba(156,199,154,0) 42%),
               radial-gradient(ellipse at 4% 30%,#b8d6a8 0 10%,rgba(184,214,168,0) 30%)}
  .logo-wreath{position:absolute;left:262px;top:405px;width:260px;height:260px;border-radius:50%;
    background:radial-gradient(circle,rgba(255,255,255,1) 0 45%,#cfe5c2 58%,#f4c9b2 72%,rgba(255,255,255,0) 74%)}
  .logo-name{position:absolute;z-index:2;left:262px;top:510px;width:260px;text-align:center;
    font-family:"Open Sans",Arial,sans-serif;font-weight:600;font-size:22px;line-height:1.15;color:var(--ink)}
  .event{position:absolute;z-index:2;width:200px;margin-left:-100px;text-align:center}
  .event-photo{display:block;width:94px;height:94px;margin:0 auto;border-radius:50%;
    border:2px solid var(--accent-orange);padding:4px;background-clip:content-box}
  .event-name{margin-top:3px;font-size:15.5px;line-height:22px;color:var(--title-text);font-weight:400}
  .event-details{margin-top:12px;font-size:11px;line-height:16px;color:var(--detail-text)}
  .cta-shapes{position:absolute;z-index:2;left:0;top:0}
  .cta-heading{position:absolute;z-index:3;left:464px;top:1006px;font-family:"Kaushan Script",cursive;
    font-size:36px;color:var(--ink);white-space:nowrap}
  .cta-url{position:absolute;z-index:3;left:462px;top:1062px;font-size:19px;color:var(--ink);white-space:nowrap}
</style>
</head>
<body>
<main class="poster">
  <div class="header-stripe"></div>
  <div class="header-band"></div>
  <div class="floral floral-top" role="img" aria-label="Watercolour peach blossoms and succulents"></div>
  <div class="floral floral-bottom" role="img" aria-label="Watercolour peach blossom, succulents and grasses"></div>
  <h1 class="poster-title">Shop Happenings</h1>

  <div class="logo-wreath" role="img" aria-label="Watercolour wreath of succulents and blossoms"></div>
  <p class="logo-name">Meadowlark<br>Petals</p>

  <section class="event" style="left:396px;top:155px">
    <span class="event-photo" role="img" aria-label="Photo of a terrarium being planted" style="background:#4e5046"></span>
    <h2 class="event-name">Terrariums &amp; Tapas</h2>
    <p class="event-details">Wed, Jan 31, 2018 at<br>5:30pm - 7:00pm EST<br>Meadowlark Petals, 1180<br>Larkspur Ln, Fernhaven,<br>SC 29999, USA</p>
  </section>

  <section class="event" style="left:166px;top:225px">
    <span class="event-photo" role="img" aria-label="Photo of roasted oysters" style="background:#8a8270"></span>
    <h2 class="event-name">Harbor Oyster<br>Farms...Roast!</h2>
    <p class="event-details">Sun, Jan 21, 2018 at<br>2:00pm - 5:00pm EST<br>Meadowlark Petals, 1180<br>Larkspur Ln, Fernhaven,<br>SC 29999, USA</p>
  </section>

  <section class="event" style="left:618px;top:225px">
    <span class="event-photo" role="img" aria-label="Photo of children wearing flower crowns" style="background:#b0463f"></span>
    <h2 class="event-name">Mother Daughter<br>Flower Crown Making</h2>
    <p class="event-details">Sat, Feb 10, 2018 at<br>10:30am - 12:00pm EST<br>Meadowlark Petals, 1180<br>Larkspur Ln, Fernhaven,<br>SC 29999, USA</p>
  </section>

  <section class="event" style="left:146px;top:513px">
    <span class="event-photo" role="img" aria-label="Photo of a mixed flower arrangement" style="background:#b44f6e"></span>
    <h2 class="event-name">Galentine's Day Flower<br>Arranging</h2>
    <p class="event-details">Tue, Feb 13, 2018 at<br>5:30pm - 7:00pm EST<br>Meadowlark Petals, 1180<br>Larkspur Ln, Fernhaven,<br>SC 29999, USA</p>
  </section>

  <section class="event" style="left:657px;top:513px">
    <span class="event-photo" role="img" aria-label="Photo of a set dinner table" style="background:#c9d3c2"></span>
    <h2 class="event-name">Valentine's Pop-up<br>Dinner</h2>
    <p class="event-details">Wed, Feb 14, 2018 at<br>6:00pm - 8:00pm EST<br>Meadowlark Petals, 1180<br>Larkspur Ln, Fernhaven,<br>SC 29999, USA</p>
  </section>

  <section class="event" style="left:301px;top:701px">
    <span class="event-photo" role="img" aria-label="Photo of a moss fairy garden terrarium" style="background:#3f5b34"></span>
    <h2 class="event-name">Fairy Garden<br>Terrariums</h2>
    <p class="event-details">Sat, Mar 3, 2018 at<br>10:30am - 12:00pm EST<br>Meadowlark Petals, 1180<br>Larkspur Ln, Fernhaven,<br>SC 29999, USA</p>
  </section>

  <section class="event" style="left:493px;top:701px">
    <span class="event-photo" role="img" aria-label="Botanical print of a mandrake plant" style="background:#5f7c55"></span>
    <h2 class="event-name">Mandrake Print<br>Making</h2>
    <p class="event-details">Wed, Mar 14, 2018 at<br>5:30pm - 7:00pm EDT<br>Meadowlark Petals, 1180<br>Larkspur Ln, Fernhaven,<br>SC 29999, USA</p>
  </section>

  <svg class="cta-shapes" width="800" height="1133" viewBox="0 0 800 1133" aria-hidden="true">
    <polygon points="693,862 590,962 800,962" fill="var(--pale-green)"/>
    <polygon points="640,962 800,908 800,1000" fill="var(--accent-orange)"/>
    <polygon points="415,1010 612,950 800,995 800,1133 432,1133" fill="var(--blush)"/>
  </svg>
  <p class="cta-heading">Visit my website</p>
  <p class="cta-url">www.meadowlarkpetals.example</p>
</main>
</body>
</html>
```